Kitchen and cabinets Landing Page design

Hi there
Web Design Task Outline
• Create a Web Design
• Uncoded webpage layout design
• Single Page - Just Homepage Layout
Task Description
* While we need to update our website, we are actually looking at working with a web designer long-term, which will include quite regular design work. So even though this is a small job, we’d love you to respond, as if you do a good job on this one, we would love to continue working with you on a more regular basis.
Please find below all the information for the design of our new website.
The current Web site is www.brindlecourt.com.au – don’t laugh!!!
Site Basics:
The site will be the landing page and online home of our kitchen renovation business. We also do vanities, bedroom robes and general cabinetery for the house and office.
Target audience:
? Predominantly home renovation seekers, families (females – decision maker) and builders.
? Most of our business comes from referrals and recommendations, but the site needs to be updated to improve our on line image
General feeling to be conveyed:
Update our old, tired 80’s site (fresh, modern and vital)
Must portray contemporary and up to date attitude - eye-catching / attention grabbing
But not too expensive looking as to alienate people who may think we look too expensive
Landing Page:
Happy to look at your creativity, but must contain a capturing image, contact details (phone), testimonials
Potential Nav Links =
Home
Photo Gallery
Contact Us
Testimonial
Vanities
Entertainment Units
Colours:
Our business has little to do with wood now so the timber look is superseded. We are open to your creative suggestions. We need all marketing media to be consistent and the website can start this process. Our logo is really weak and dated as well. At present we have a green and blue business card with capital BC logo (hmmm), but we’re generally thinking something that represents the home and kitchen
Layout: Open to your creativity
* Samples of Other Good (Similar) Sites We Like:
www.hobnookrooms.com.au
www.pimlu.com.au
www.foremostgalleys.com.au/
www.trimhaven.com.au
www.thebakingmanor.com.au
Header Text =
Feel free to submit something from your own creative ideas.
Header Image/photo Ideas:
As the site is about kitchen and house hold cabinets, feel free to use an image to reflect that. We are generally thinking to have one main image that is quite eye-catching and attention grabbing. We can supply photos from jobs we have done later.
* Notes:
1. Do not feel completely bound to these ideas. Feel free to convey the basic idea however your creativity desires.
Thanks a lot and look forward to receiving your first design!
Cheers
Gareth
Updates
sorry people - forgot to mention our best selling point!
we were established in 1980, so have been going for 30 years. This is a strong selling point.
We use "30 years of excellence" as a tag.
there are numerous ways of using est. 1980, ie gold label, starburst etc. Go for it.
thanks
Gareth
Hi Designers, My apologies for the delay in responding to your designs. I have been working on other business and have not had a chance to look at them thoroughly. I plan to focus on them today and will provide feedback. Thank you for your understanding.
Reason: Today was the first chance I've had to look at designs. Will be actively providing feedback over next fews day. Am looking to make some changes to the a few of the designs received. Thanks everyone for you patience.

```html
<!DOCTYPE html>
<html lang="en">
<head>
<meta charset="utf-8">
<title>Brindle Court Cabinets &amp; Furniture</title>
<link rel="stylesheet" href="https://fonts.googleapis.com/css2?family=Arimo:wght@400;700&family=Cormorant+Garamond:ital,wght@1,500&family=Tinos&display=swap">
<style>
  :root {
    --timber-light: #e9a75c;
    --timber: #d88a3c;
    --timber-dark: #b86c24;
    --accent: #d27e1e;
    --ink: #4a4a4a;
    --ink-soft: #5a5a5a;
    --heading: #555555;
    --rule: #8a8a8a;
    --page-top: #d9d9d9;
    --page-bottom: #ffffff;
    --white: #ffffff;
    --arrow: #b2754a;
  }
  * { margin: 0; padding: 0; box-sizing: border-box; }
  html, body { width: 1164px; height: 1200px; overflow: hidden; }
  body {
    position: relative;
    font-family: "Arimo", Arial, sans-serif;
    color: var(--ink);
    background: linear-gradient(to bottom, var(--page-top) 160px, #e8e8e8 560px, var(--page-bottom) 760px, var(--page-bottom));
  }

  /* Header */
  .site-header {
    position: absolute; left: 0; top: 0; width: 1164px; height: 159px;
    background: linear-gradient(to bottom, var(--timber-light), var(--timber) 55%, #cf8237);
    box-shadow: 0 3px 5px rgba(0,0,0,.35);
  }
  .brand {
    position: absolute; left: 44px; top: 34px;
    display: flex; align-items: center; gap: 12px;
  }
  .brand-dot {
    width: 70px; height: 70px; border-radius: 50%;
    background: #f3e6d2;
  }
  .brand-name {
    font-family: "Tinos", "Times New Roman", serif;
    font-size: 26px; line-height: 1.15; color: #5a2d0f; width: 190px;
  }
  .contact-card {
    position: absolute; left: 792px; top: 10px;
    display: flex; gap: 16px; align-items: flex-start;
  }
  .contact-lines {
    font-weight: 700; font-size: 15.5px; line-height: 20.5px; color: var(--white);
    text-shadow: 0 1px 2px rgba(0,0,0,.45); padding-top: 2px;
  }
  .main-nav {
    position: absolute; right: 36px; top: 99px;
    display: flex; gap: 8px;
  }
  .main-nav a {
    display: block; padding: 12px 15px; font-size: 19px; color: var(--white);
    text-decoration: none; text-shadow: 0 1px 2px rgba(0,0,0,.4); border-radius: 3px;
  }
  .main-nav a.is-active {
    background: rgba(255,255,255,.22); border: 1px solid rgba(255,255,255,.55);
  }

  /* Showcase */
  .showcase { position: absolute; left: 0; top: 159px; width: 1164px; height: 440px; }
  .frame {
    position: absolute; background: var(--white); border-radius: 4px;
    box-shadow: 0 2px 6px rgba(0,0,0,.3); padding: 8px;
  }
  .frame .photo { width: 100%; height: 100%; }
  .frame-left { left: 76px; top: 91px; width: 246px; height: 304px; }
  .frame-right { left: 841px; top: 91px; width: 245px; height: 304px; }
  .frame-center { left: 318px; top: 66px; width: 529px; height: 354px; z-index: 2; }
  .photo-floor { background: linear-gradient(to bottom, #efece6 0%, #e6e1d8 50%, #9c3b1c 62%, #6e2210 100%); }
  .photo-kitchen { background: linear-gradient(to bottom, #e9e4da 0%, #dcd6cb 45%, #f2efe9 60%, #c9c3b8 80%, #5e2a16 100%); }
  .photo-island { background: linear-gradient(to bottom, #e5e0d6 0%, #d8d2c6 40%, #eeeae3 60%, #bdb6aa 100%); }
  .slide-arrow { position: absolute; top: 214px; }
  .slide-arrow.prev { left: 34px; }
  .slide-arrow.next { left: 1098px; }

  /* Tagline */
  .tagline {
    position: absolute; left: 43px; top: 638px; width: 1078px; height: 69px;
    border-top: 1px solid var(--rule); border-bottom: 1px solid var(--rule);
    font-family: "Cormorant Garamond", Georgia, serif; font-style: italic; font-weight: 500;
    font-size: 44px; line-height: 67px; text-align: center; color: var(--ink);
  }

  /* Columns */
  .column { position: absolute; top: 742px; }
  .column h2 {
    font-family: "Tinos", "Times New Roman", serif; font-weight: 400;
    font-size: 27px; color: var(--heading); letter-spacing: .3px; margin-bottom: 14px;
  }
  .mission { left: 39px; width: 340px; }
  .mission p { font-size: 13.6px; line-height: 16.5px; margin: 0 0 16.5px 5px; width: 330px; color: var(--ink-soft); }
  .testimonials { left: 449px; width: 300px; }
  .quote { position: relative; padding-left: 32px; margin-bottom: 19px; }
  .quote .bullet { position: absolute; left: 3px; top: 1px; }
  .quote h3 { font-size: 14px; font-weight: 700; color: var(--accent); line-height: 18px; margin-bottom: 9px; }
  .quote p { font-size: 13.6px; line-height: 27px; color: var(--ink-soft); }
  .consultation { left: 802px; width: 335px; }
  .consultation p { font-size: 13.6px; line-height: 27px; color: var(--ink-soft); }
  .consultation a { color: var(--accent); }
  .more-link {
    position: absolute; top: 1087px; font-size: 12px; color: var(--accent);
    text-decoration: underline; text-transform: uppercase;
  }
  .more-link.mission-more { left: 298px; }
  .more-link.testimonial-more { left: 617px; }

  /* Footer */
  .site-footer {
    position: absolute; left: 0; top: 1147px; width: 1164px; height: 53px;
    background: linear-gradient(to bottom, #f0c48e, var(--timber) 40%, var(--timber-dark));
    border-top: 1px solid #c9c9c9;
    font-size: 12px; color: var(--white); text-align: center; line-height: 52px;
  }
</style>
</head>
<body>
  <header class="site-header">
    <div class="brand">
      <span class="brand-dot"></span>
      <span class="brand-name">Brindle Court Cabinets &amp; Furniture</span>
    </div>
    <div class="contact-card">
      <svg width="72" height="86" viewBox="0 0 72 86" aria-hidden="true">
        <rect x="6" y="4" width="62" height="78" rx="4" fill="#b57d1f"/>
        <rect x="6" y="4" width="62" height="78" rx="4" fill="none" stroke="#7a4e10" stroke-width="2"/>
        <rect x="2" y="14" width="8" height="6" fill="#ddd"/>
        <rect x="2" y="30" width="8" height="6" fill="#ddd"/>
        <rect x="2" y="46" width="8" height="6" fill="#ddd"/>
        <rect x="2" y="62" width="8" height="6" fill="#ddd"/>
        <text x="40" y="56" text-anchor="middle" font-family="Arimo, Arial, sans-serif" font-size="38" font-weight="700" fill="#ffffff">@</text>
      </svg>
      <div class="contact-lines">
        Unit 5, 418 Larkspur Road,<br>
        Wattlebank, VIC<br>
        Tel. 03 9481-2270<br>
        Fax. 03 9481-2271
      </div>
    </div>
    <nav class="main-nav">
      <a class="is-active" href="#">Home</a>
      <a href="#">Photo Gallery</a>
      <a href="#">Contact Us</a>
      <a href="#">Testimonial</a>
      <a href="#">Vanities</a>
      <a href="#">Entertainment Units</a>
    </nav>
  </header>

  <section class="showcase">
    <svg class="slide-arrow prev" width="32" height="50" viewBox="0 0 32 50" aria-hidden="true">
      <polyline points="26,4 8,25 26,46" fill="none" stroke="var(--arrow)" stroke-width="6" stroke-linecap="round" stroke-linejoin="round"/>
    </svg>
    <div class="frame frame-left"><div class="photo photo-floor" role="img" aria-label="Open-plan room with white walls and polished timber floor"></div></div>
    <div class="frame frame-center"><div class="photo photo-island" role="img" aria-label="White kitchen with large island bench and stainless steel appliances"></div></div>
    <div class="frame frame-right"><div class="photo photo-kitchen" role="img" aria-label="White kitchen cabinetry with wall ovens and cooktop"></div></div>
    <svg class="slide-arrow next" width="32" height="50" viewBox="0 0 32 50" aria-hidden="true">
      <polyline points="6,4 24,25 6,46" fill="none" stroke="var(--arrow)" stroke-width="6" stroke-linecap="round" stroke-linejoin="round"/>
    </svg>
  </section>

  <h1 class="tagline">Creating Style and Comfort with Cutting-Edge Technology...</h1>

  <section class="column mission">
    <h2>OUR MISSION:</h2>
    <p>To produce excellent quality cabinetry<br>every time!</p>
    <p>We cater for those who truly care about quality, workmanship and a high level of personal service. We are proud of ourinnovative designs, superior products, and outstanding service sought after by the discerning customers.</p>
    <p>We custom design, build and install quality cabinets, kitchens, theatre entertainment units, furniture, stone bench tops and stainless steel finishes. Customized work and architectural designs back up with professional advice and personalised service.</p>
    <p>We guarantee all jobs on time and on budget......</p>
  </section>

  <section class="column testimonials">
    <h2>TESTIMONIALS:</h2>
    <div class="quote">
      <svg class="bullet" width="16" height="16" viewBox="0 0 16 16" aria-hidden="true"><circle cx="8" cy="8" r="7" fill="#a9a9a9"/><polygon points="6,4.5 11,8 6,11.5" fill="#fff"/></svg>
      <h3>Lorem ipsum Client</h3>
      <p>Lorem ipsum dolor sit amet consecutor.<br>Lorem ipsum dolor sit amet consecutor.</p>
    </div>
    <div class="quote">
      <svg class="bullet" width="16" height="16" viewBox="0 0 16 16" aria-hidden="true"><circle cx="8" cy="8" r="7" fill="#a9a9a9"/><polygon points="6,4.5 11,8 6,11.5" fill="#fff"/></svg>
      <h3>Lorem ipsum Client</h3>
      <p>Lorem ipsum dolor sit amet consecutor.<br>Lorem ipsum dolor sit amet consecutor.</p>
    </div>
    <div class="quote">
      <svg class="bullet" width="16" height="16" viewBox="0 0 16 16" aria-hidden="true"><circle cx="8" cy="8" r="7" fill="#a9a9a9"/><polygon points="6,4.5 11,8 6,11.5" fill="#fff"/></svg>
      <h3>Lorem ipsum Client</h3>
      <p>Lorem ipsum dolor sit amet consecutor.<br>Lorem ipsum dolor sit amet consecutor.</p>
    </div>
  </section>

  <section class="column consultation">
    <h2>CONSULTATION</h2>
    <p>For a Obligation FREE consultation and quotation, email us - <a href="#">jenna@brindlecourt.com.au</a> or call us now on 03 9481 2270</p>
  </section>

  <a class="more-link mission-more" href="#">Read more</a>
  <a class="more-link testimonial-more" href="#">All testimonials</a>

  <footer class="site-footer">Brindlecourtcabinets&amp;furniture &copy; 2011 . All Rights Reserved</footer>
</body>
</html>
```